COVER ONLY - Electrical supply company needs new catalogue cover (front and back)

We're currently finalising our catalogue and have gone through many changes in branding since our last catalogue so need a completely NEW design incorporating the new logo and design feel from the CI document attached.

Since the company is moving more corporate we'd like a much cleaner looking cover (front and back) from what we had before. We'd would like to keep a dominate color for the year so we can simply change the color for the following year catalogue.

We'd like to show product images (supplied) on the front of the catalogue but not as dominate as our previous catalogue (attached to get an idea of where we came from).

We'd like to introduce as much of our new CI into the new catalogue cover as possible while keeping up with our new corporate style of "clean and neat".

I've attached our logo, CI guide, old catalogue cover and some product images.

We would like the file to be handed over in complete format as well as in .psd

(Our website is also being updated but the old website is still up www.qv.co.za)
Updates

Cover size is A4 and the spine will be roughly 3/4 inch.

Please make sure you read the CI guide.

Produce something that shows professionalism, class and style.  We want something that any multi national billion dollar company would be proud to show

Industry/Entity Type

Electrical

Font styles to use
Other font styles liked:
• Sansation

```html
<!DOCTYPE html>
<html lang="en">
<head>
<meta charset="utf-8">
<title>QuantaVolt Catalogue Cover</title>
<link href="https://fonts.googleapis.com/css2?family=Open+Sans:ital,wght@0,400;0,600;0,700;1,700&display=swap" rel="stylesheet">
<style>
:root{
  --blue:#29a0dc;
  --blue-light:#7cc6ee;
  --sky:#e8f4fb;
  --ink:#3a3f44;
  --heading:#2b3b4b;
  --grey:#7a7a7a;
  --contact-a:#5b5b5b;
  --contact-b:#3b4e5b;
  --white:#ffffff;
}
*{margin:0;padding:0;box-sizing:border-box}
html,body{width:1200px;height:854px;overflow:hidden;background:var(--white)}
.cover{position:relative;width:1200px;height:854px;font-family:"Open Sans",Arial,sans-serif;color:var(--ink);overflow:hidden}
.backdrop{position:absolute;inset:0}
.back-panel{position:absolute;left:54px;top:108px;width:520px;font-size:13px;line-height:17px}
.section-title{font-size:15.5px;font-weight:600;color:var(--heading);margin-bottom:20px}
.section-title + p{margin-bottom:17px}
.group{margin-bottom:17px}
.brands{margin-bottom:18px}
.contact{position:absolute;left:0;top:682px;width:598px;height:172px;background:linear-gradient(90deg,var(--contact-a),var(--contact-b));color:var(--white);font-size:13.5px;line-height:17px}
.contact-title{position:absolute;left:0;width:578px;top:6px;text-align:center;font-size:24px;font-weight:600}
.contact-col{position:absolute}
.contact-col.cape{left:69px;top:66px}
.contact-col.bay{left:356px;top:49px}
.products{position:absolute;left:740px;top:172px;width:395px;height:480px;border-radius:6px;background:radial-gradient(ellipse at 40% 45%,#5d6168 0%,#8c9399 45%,rgba(220,232,240,0) 75%)}
.brand{position:absolute;left:888px;top:32px;display:flex;align-items:center;gap:12px}
.brand-mark{width:26px;height:26px;background:var(--blue)}
.brand-name{font-size:30px;font-weight:400;color:var(--grey)}
.tagline{position:absolute;left:620px;top:643px;color:var(--white);font-size:26px;line-height:36px}
.tagline em{font-weight:700;font-style:italic}
.tagline strong{font-weight:700}
.website{position:absolute;left:1051px;top:824px;font-size:13.5px;font-weight:600;color:var(--heading)}
</style>
</head>
<body>
<div class="cover">
  <svg class="backdrop" width="1200" height="854" viewBox="0 0 1200 854" aria-hidden="true">
    <defs>
      <linearGradient id="blueField" x1="0" y1="0" x2="1" y2="1">
        <stop offset="0" stop-color="#8fcdf0"/>
        <stop offset="0.5" stop-color="#3aa8e0"/>
        <stop offset="1" stop-color="#1f98d6"/>
      </linearGradient>
      <linearGradient id="skyField" x1="0" y1="0" x2="1" y2="1">
        <stop offset="0" stop-color="#cfe8f7"/>
        <stop offset="1" stop-color="#f4f9fc"/>
      </linearGradient>
    </defs>
    <rect width="1200" height="854" fill="url(#skyField)"/>
    <polygon points="0,0 700,0 935,854 0,854" fill="url(#blueField)"/>
    <polygon points="0,0 450,0 610,854 0,854" fill="#ffffff" opacity="0.55"/>
    <polygon points="0,128 0,168 580,854 620,854" fill="#ffffff" opacity="0.6"/>
    <polygon points="470,0 500,0 740,854 712,854" fill="#ffffff" opacity="0.25"/>
  </svg>

  <section class="back-panel">
    <h2 class="section-title">A : relays</h2>
    <p>PCB, plug-in, step, miniature industrial and power relays; relay interface modules; sockets; daylight switches; solid-state relays and accessories</p>
    <p class="brands">Brands: Relvo, Solidor</p>

    <h2 class="section-title">B : motor control</h2>
    <div class="group">Control and protection<br>• Contactors • Semi-conductor contactors • Thermal overload relays<br>• Motor control circuit breakers • Motor starters • Soft starters<br>• IC soft starters • Electronic motor protection</div>
    <div class="group">Command and signalling<br>• Pushbuttons and selectors • Signal towers and beacons<br>• Limit and foot switches • Rotary cam switches<br>• Joystick controls • Pendant controls •Wormgear limit switches</div>
    <div class="group">Switching and circuit protection<br>• Load break switches • Earth leakage relays</div>
    <div class="group">Automation and control<br>• Time relays • Protection relays • Level control relays<br>• Programmable logic relays • Switching power supplies</div>
    <div class="group">Energy management<br>• Metering instruments (kwh) • Automatic power factor controllers<br>• Automatic battery chargers • Automatic transfer switch controllers<br>• Engine and generator controllers</div>
    <p>Brands: Marvento, Kairo, Protek, MC Drives</p>
  </section>

  <footer class="contact">
    <h2 class="contact-title">Contact</h2>
    <div class="contact-col cape">Cape Province<br>5 Elmbrook Business Park<br>Harbour Road<br>Marine Gardens<br>Seaview</div>
    <div class="contact-col bay">7520&nbsp; P.O. Box 40982<br>Riverside<br>4050 Bayton<br>Telephone: 010 555 0184<br>Telefax: 010 555 0193<br>Email: info@qv.co.za</div>
  </footer>

  <div class="brand">
    <span class="brand-mark"></span>
    <span class="brand-name">QuantaVolt</span>
  </div>

  <div class="products" role="img" aria-label="Product group: variable speed drive, circuit breaker, energy controller, rotary isolator and load break switch"></div>

  <p class="tagline">Dedicated<br>supliers of quality<br><em>products &amp; sevice at</em><br>competitivew<br><strong>prices</strong></p>

  <div class="website">www.qv.co.za</div>
</div>
</body>
</html>
```